Website for Briar Hollow Gathering Church

Wordpress website design required for Briar Hollow Gathering Church. We are a family oriented church catering for age groups from school age to elderly people. The church has a wide variety of activities which it coordinates. The idea is to describe the activities on the activities page, but cross-link them to show which would be applicable to the different age groups.

We would like an inviting website which is easy to read and navigate.

Target Market(s)

Very wide audience - from school age youth to elderly people, so design and style should cater for both audiences.

Industry/Entity Type

Church

Coding

Coded - Design and coding required

Number of Pages Required

5+ page

Font styles to use
Sans Serif

Colors
0255a3
ffffff
0792cd
f78f20

Requirements
Must have
• Inviting website.
• Clear readable font.
• Space to import photos to balance text on each page.
• Need to project a dynamic and progressive feel for the church.
• Easy to navigate.
Nice to have
• Scrolling photos on pages. Ability to enter questions/ comments/prayer requests on Home page.
Should not have
• Conservative audience, so should not be too bold.

```html
<!DOCTYPE html>
<html lang="en">
<head>
<meta charset="utf-8">
<title>Briar Hollow Gathering Church</title>
<link rel="stylesheet" href="https://fonts.googleapis.com/css2?family=Bitter:wght@400;700&family=Roboto:wght@400;500;700&display=swap">
<style>
:root{
  --blue:#0255a3;
  --sky:#0792cd;
  --orange:#f78f20;
  --white:#ffffff;
  --ink:#222222;
  --grey-band:#f1f1f1;
  --charcoal:#333333;
  --footer-bar:#1c9ad2;
}
*{box-sizing:border-box;margin:0;padding:0}
html,body{width:1200px;height:2302px;overflow:hidden}
body{position:relative;background:var(--white);font-family:"Roboto",Arial,sans-serif;color:var(--ink)}
a{text-decoration:none}
.abs{position:absolute}
.heading{font-family:"Bitter",Georgia,serif;font-weight:700}

/* header */
.site-header{left:0;top:0;width:1200px;height:138px;background:var(--white)}
.brand{left:132px;top:86px;display:flex;align-items:center;gap:8px;font-family:"Bitter",Georgia,serif;font-size:23px;color:var(--blue)}
.brand-dot{width:14px;height:14px;border-radius:50%;background:var(--blue)}
.search{left:709px;top:18px;width:148px;height:54px;border:1px solid #cfcfcf;border-radius:4px;display:flex;align-items:center;font-size:12px;color:#999}
.search .icon{width:40px;height:100%;display:flex;align-items:center;justify-content:center;border-right:1px solid #ddd;margin-right:12px}
.call{left:880px;top:18px;width:188px;height:54px;background:var(--blue);border-radius:5px;display:flex;align-items:center;padding-left:10px;color:var(--white)}
.call .ring{width:38px;height:38px;border-radius:50%;background:var(--sky);display:flex;align-items:center;justify-content:center;margin-right:12px}
.call small{display:block;font-size:9px;font-weight:700;letter-spacing:.3px}
.call strong{display:block;font-size:20px;font-weight:700}
.main-nav{left:531px;top:94px;height:44px;display:flex;font-family:"Bitter",Georgia,serif;font-size:13px}
.main-nav a{display:flex;align-items:center;color:#222}
.main-nav a.current{background:var(--orange);color:var(--white);width:65px;justify-content:center;font-weight:700}

/* hero */
.hero{left:0;top:138px;width:1200px;height:453px;background:linear-gradient(180deg,#d9d6d2 0%,#8a7a6e 55%,#5a3a2a 100%)}
.hero-caption{left:0;top:398px;width:1200px;text-align:center;font-family:"Bitter",Georgia,serif;font-size:33px;line-height:45px;color:var(--white)}
.hero-arrow{top:344px;width:43px;height:43px;background:rgba(255,255,255,.55);display:flex;align-items:center;justify-content:center}
.hero-dots{left:0;top:530px;width:1200px;display:flex;justify-content:center;gap:14px;align-items:center}
.hero-dots span{width:9px;height:9px;border-radius:50%;background:var(--white)}
.hero-dots span.active{width:13px;height:13px;background:transparent;border:2px solid var(--white)}

/* welcome */
.band-grey{left:0;top:591px;width:1200px;height:330px;background:var(--grey-band)}
.welcome{left:132px;top:617px;width:936px;height:323px;background:var(--white);border:4px solid #e6e6e6;border-bottom:none;padding:36px 40px 0}
.welcome h1{font-size:22px;color:var(--blue);margin-bottom:14px}
.welcome p{font-size:12px;line-height:19px;width:560px;margin-bottom:19px;color:#333}
.welcome p.lead{font-weight:500;color:#222}
.btn{display:inline-block;background:var(--orange);color:var(--white);font-family:"Roboto",Arial,sans-serif;font-weight:700;font-size:12px;text-transform:uppercase;text-decoration:none}
.welcome .btn{padding:11px 13px}

/* tiles */
.tile{width:470px;color:var(--white);text-align:center}
.tile h2{font-size:22px;margin:14px 0 12px}
.tile .text{font-size:12.5px;line-height:19px}
.t-prayer{left:130px;top:940px;height:297px;background:var(--blue);padding-top:26px}
.t-contact{left:599px;top:940px;height:297px;background:var(--orange);padding-top:26px}
.t-times{left:130px;top:1237px;height:336px;background:var(--charcoal);padding-top:24px}
.t-quick{left:599px;top:1237px;width:471px;height:336px;background:var(--sky);padding-top:22px}
.field{background:var(--white);color:#555;font-size:11px;display:flex;align-items:center;padding-left:16px;text-align:left}
.prayer-field{position:absolute;left:51px;top:204px;width:369px;height:47px;border:3px solid #e2e2e2}
.prayer-field .go{position:absolute;right:8px;top:7px;width:60px;height:29px;background:var(--orange);display:flex;align-items:center;justify-content:center}
.times{margin:18px 0 0 128px;width:260px;font-size:12.5px;text-align:left;border-collapse:collapse}
.times td{height:28px}
.times td:nth-child(1){width:107px}
.times td:nth-child(2){width:37px}
.quick .field{position:absolute;width:207px;height:37px;padding-left:15px}
.quick .msg{align-items:flex-start;padding-top:12px}
.send{position:absolute;left:362px;top:280px;width:86px;height:38px;display:flex;align-items:center;justify-content:center;font-size:15px}

/* news */
.news-band{left:0;top:1540px;width:1200px;height:470px}
.news-title{left:130px;top:1613px;font-size:21px;color:var(--white)}
.all-news{left:949px;top:1612px;width:121px;height:33px;background:var(--sky);display:flex;align-items:center;justify-content:center;font-size:11px}
.card{top:1670px;width:296px;height:284px;border:2px solid var(--white);color:var(--white);padding:22px 20px 0 20px}
.card .mark{position:absolute;left:20px;top:24px;width:27px;height:27px;background:var(--orange);display:flex;align-items:center;justify-content:center}
.card h3{margin-left:44px;font-size:13.5px;line-height:19px;margin-bottom:12px}
.card p{margin-left:44px;font-size:11px;line-height:18px;text-align:justify}
.card .btn{position:absolute;left:66px;bottom:26px;padding:7px 12px;font-size:11px}

/* footer */
.site-footer{left:0;top:2008px;width:1200px;height:253px;background:var(--sky)}
.foot-brand{left:132px;top:2054px;width:279px;height:126px;background:var(--white);display:flex;align-items:center;justify-content:center;gap:7px;font-family:"Bitter",Georgia,serif;font-size:17px;color:var(--blue)}
.foot-col{top:2050px;color:var(--white)}
.foot-col h4{font-family:"Bitter",Georgia,serif;font-size:15px;margin-bottom:18px}
.foot-col ul{list-style:none;font-size:12px}
.foot-col li{height:24px}
.social li{display:flex;align-items:center;height:32px}
.social .dot{width:9px;height:9px;border-radius:50%;background:var(--white);margin:0 17px 0 3px}
.news-field{position:absolute;left:0;top:38px;width:253px;height:44px}
.signup{position:absolute;left:159px;top:98px;width:94px;height:41px;display:flex;align-items:center;justify-content:center;font-size:15px}
.copy{left:0;top:2261px;width:1200px;height:41px;background:var(--footer-bar);color:var(--white);font-size:12px;display:flex;align-items:center;justify-content:center}
</style>
</head>
<body>

<header class="abs site-header">
  <div class="abs brand"><span class="brand-dot"></span>Briar Hollow Gathering Church</div>
  <div class="abs search"><span class="icon"><svg width="12" height="12" viewBox="0 0 12 12"><circle cx="5" cy="5" r="3.6" fill="none" stroke="#555" stroke-width="1.6"/><line x1="7.7" y1="7.7" x2="11" y2="11" stroke="#555" stroke-width="1.6"/></svg></span>Search</div>
  <div class="abs call">
    <span class="ring"><svg width="18" height="18" viewBox="0 0 24 24"><path d="M6.6 10.8a15 15 0 0 0 6.6 6.6l2.2-2.2a1 1 0 0 1 1-.25 11.4 11.4 0 0 0 3.6.57 1 1 0 0 1 1 1V20a1 1 0 0 1-1 1A17 17 0 0 1 3 4a1 1 0 0 1 1-1h3.5a1 1 0 0 1 1 1c0 1.250.2 2.45.57 3.57a1 1 0 0 1-.25 1z" fill="#fff"/></svg></span>
    <span><small>CALL US NOW</small><strong>9400 2718</strong></span>
  </div>
  <nav class="abs main-nav">
    <a class="current" href="#">Home</a>
    <a href="#" style="margin-left:23px">Age Group</a>
    <a href="#" style="margin-left:41px">Activities</a>
    <a href="#" style="margin-left:40px">Events&nbsp; Calendar</a>
    <a href="#" style="margin-left:30px">About</a>
    <a href="#" style="margin-left:31px">Contact</a>
  </nav>
</header>

<section class="abs hero" role="img" aria-label="Photo of the congregation gathered for a shared meal in the church hall"></section>
<div class="abs hero-arrow" style="left:89px"><svg width="12" height="16" viewBox="0 0 12 16"><path d="M9 2 3 8l6 6" fill="none" stroke="#222" stroke-width="2.5"/></svg></div>
<div class="abs hero-arrow" style="left:1067px"><svg width="12" height="16" viewBox="0 0 12 16"><path d="m3 2 6 6-6 6" fill="none" stroke="#222" stroke-width="2.5"/></svg></div>
<div class="abs hero-caption">Blessings from Briar Hollow<br>Gathering Church !</div>
<div class="abs hero-dots"><span></span><span class="active"></span><span></span><span></span><span></span></div>

<div class="abs band-grey"></div>
<section class="abs welcome">
  <h1 class="heading">Welcome to our site</h1>
  <p class="lead">Thank you for visiting our website. We would like to invite you to join us for worship at our church on 14 Wren Lane, Briar Hollow.</p>
  <p>We hold two services which are at 8 am (traditional worship service where we sing hymns) and at 10 am (family worship service) where the children would head off to join the Little Sprouts, Kids Corner or (Junior) Spark during the sermon.</p>
  <p>Holy Communion is generally held on the 3rd Sunday of the month.</p>
  <a class="btn" href="#">Read More</a>
</section>

<section class="abs tile t-prayer">
  <svg width="62" height="40" viewBox="0 0 62 40"><path d="M4 22h10v14H4zM14 24c6-4 12-6 18-4l10 3c3 1 2 5-1 5H30M14 34c10 3 18 3 26-1l16-10c3-2 0-6-3-5l-13 6" fill="none" stroke="#fff" stroke-width="2.4" stroke-linejoin="round"/><path d="M26 14c4-8 14-12 22-8" fill="none" stroke="#fff" stroke-width="2.4"/></svg>
  <h2 class="heading">Prayer Request</h2>
  <p class="text">Share a prayer and our team will<br>hold it in prayer this week</p>
  <div class="field prayer-field">
    <svg width="13" height="10" viewBox="0 0 13 10" style="margin-right:16px"><rect x=".7" y=".7" width="11.6" height="8.6" fill="none" stroke="#555" stroke-width="1.3"/><path d="m1 1 5.5 4.5L12 1" fill="none" stroke="#555" stroke-width="1.3"/></svg>E mail id
    <span class="go"><svg width="34" height="12" viewBox="0 0 34 12"><path d="M0 6h30M24 1l7 5-7 5" fill="none" stroke="#fff" stroke-width="2.6"/></svg></span>
  </div>
</section>

<section class="abs tile t-contact">
  <svg width="50" height="36" viewBox="0 0 50 36"><rect x="1.5" y="1.5" width="47" height="33" fill="none" stroke="#fff" stroke-width="2.6"/><path d="m2 2 23 18L48 2M2 34l17-16M48 34 31 18" fill="none" stroke="#fff" stroke-width="2.6"/></svg>
  <h2 class="heading">Contact Us</h2>
  <p class="text">Briar Hollow Gathering Church – 14<br>Wren Lane, Briar Hollow,<br>6200 Australia.</p>
  <p class="text" style="margin-top:19px">T : <b>9400 2718</b><br>E : <b>office@briarhollow.example.org</b></p>
</section>

<section class="abs tile t-times">
  <svg width="48" height="48" viewBox="0 0 48 48"><circle cx="24" cy="24" r="21.5" fill="none" stroke="#fff" stroke-width="2.6"/><path d="M24 10v15h9" fill="none" stroke="#fff" stroke-width="2.6"/></svg>
  <h2 class="heading">Service Times</h2>
  <table class="times">
    <tr><td>Monday</td><td>:</td><td>09:00 am - 9.00 pm</td></tr>
    <tr><td>Tuesday</td><td>:</td><td>09:00 am - 9.00 pm</td></tr>
    <tr><td>Wednesday</td><td>:</td><td>09:00 am - 9.00 pm</td></tr>
    <tr><td>Thursday</td><td>:</td><td>09:00 am - 9.00 pm</td></tr>
    <tr><td>Friday</td><td>:</td><td>09:00 am - 9.00 pm</td></tr>
    <tr><td>Saturday</td><td>:</td><td>09:00 am - 9.00 pm</td></tr>
  </table>
</section>

<section class="abs tile t-quick quick">
  <svg width="48" height="42" viewBox="0 0 48 42"><path d="M46 2 2 20l14 5 4 15 7-10 11 8z" fill="#fff"/><path d="M16 25 46 2 20 28" fill="none" stroke="#0792cd" stroke-width="2"/></svg>
  <h2 class="heading" style="margin-top:6px">Quick Contact</h2>
  <div class="field" style="left:24px;top:132px">Name</div>
  <div class="field" style="left:24px;top:180px">E mail</div>
  <div class="field" style="left:24px;top:232px">Phone</div>
  <div class="field msg" style="left:241px;top:132px;height:137px">Message</div>
  <span class="btn send">Send</span>
</section>

<svg class="abs news-band" viewBox="0 0 1200 470" preserveAspectRatio="none" aria-hidden="true"><path d="M0 60Q600 0 1200 60V470H0z" fill="#0255a3"/></svg>
<h2 class="abs heading news-title">Latest News</h2>
<a class="abs btn all-news" href="#">Read All News</a>

<article class="abs card" style="left:132px">
  <span class="mark"><svg width="8" height="12" viewBox="0 0 8 12"><path d="m1 1 5 5-5 5" fill="none" stroke="#fff" stroke-width="2"/></svg></span>
  <h3 class="heading">Understanding Death and Suffering</h3>
  <p>Briar Hollow Gathering Church, 14 Wren Lane, Briar Hollow, 6200 Australia+ Area Map Click on UnderstandingDeathAndSuffering for flyer An Invitation Is it possible to die well? How can we cope better with suffering, pain and grief? Is euthanasia an answer?</p>
  <a class="btn" href="#">Read More</a>
</article>
<article class="abs card" style="left:453px">
  <span class="mark"><svg width="8" height="12" viewBox="0 0 8 12"><path d="m1 1 5 5-5 5" fill="none" stroke="#fff" stroke-width="2"/></svg></span>
  <h3 class="heading">Riverside Women’s Convention – 2 Thessalonians ‘Waiting for the Day’</h3>
  <p>Speaker, Marisa Holt serves as Dean of Women at Hillcrest College in Lakeford, where she co-ordinates the Ministry Training for Women course.She also ministers with her husband Owen at Elmfield Community ...</p>
  <a class="btn" href="#">Read More</a>
</article>
<article class="abs card" style="left:772px">
  <span class="mark"><svg width="8" height="12" viewBox="0 0 8 12"><path d="m1 1 5 5-5 5" fill="none" stroke="#fff" stroke-width="2"/></svg></span>
  <h3 class="heading">Trailblazers Youth Spring Camps</h3>
  <p>Invite a friend to camp this season and get $40 off your next camp ! Help someone ‘live it with Spirit’ this coming school holidays by inviting them to a camp ! This season we are running a number of exciting camps for young people who are in primary and secondary school such ...</p>
  <a class="btn" href="#">Read More</a>
</article>

<footer class="abs site-footer"></footer>
<div class="abs foot-brand"><span class="brand-dot" style="width:11px;height:11px"></span>Briar Hollow Gathering Church</div>
<div class="abs foot-col" style="left:488px">
  <h4>Menu</h4>
  <ul><li>Home</li><li>Age group</li><li>Activites</li><li>Teams</li><li>Contact Us</li></ul>
</div>
<div class="abs foot-col social" style="left:643px">
  <h4>Follow us</h4>
  <ul style="margin-top:-8px"><li><span class="dot"></span>Gatherly</li><li><span class="dot"></span>Chirpline</li><li><span class="dot"></span>Linkwell</li><li><span class="dot"></span>RSS Feed</li></ul>
</div>
<div class="abs foot-col" style="left:817px;width:253px;height:150px">
  <h4>Newsletter!</h4>
  <div class="field news-field"><svg width="13" height="10" viewBox="0 0 13 10" style="margin-right:12px"><rect x=".7" y=".7" width="11.6" height="8.6" fill="none" stroke="#555" stroke-width="1.3"/><path d="m1 1 5.5 4.5L12 1" fill="none" stroke="#555" stroke-width="1.3"/></svg>E mail id</div>
  <span class="btn signup">Signup!</span>
</div>
<div class="abs copy">Copyrights @ 2016 All Rights Reserved</div>

</body>
</html>
```